New letter head for Air Conditioning business

We need a new professional letter head design to suit our new re-branded air conditioning business. Our new logo is attached

```html
<!DOCTYPE html>
<html lang="en">
<head>
<meta charset="utf-8">
<title>Norvale Letterhead</title>
<link href="https://fonts.googleapis.com/css2?family=Open+Sans:wght@400;600;700&family=Dancing+Script&display=swap" rel="stylesheet">
<style>
  :root {
    --backdrop: #e9e9ea;
    --paper: #ffffff;
    --coral: #ef6a5e;
    --green: #4fb97a;
    --charcoal: #3a3a3c;
    --ink: #7a7a7c;
    --ink-dark: #555558;
    --white: #ffffff;
  }
  * { box-sizing: border-box; margin: 0; padding: 0; }
  html, body { width: 1200px; height: 795px; overflow: hidden; }
  body {
    background: var(--backdrop);
    font-family: "Open Sans", Arial, sans-serif;
    position: relative;
  }
  .letterhead {
    position: absolute;
    left: 338px; top: 27px;
    width: 524px; height: 740px;
    background: var(--paper);
    box-shadow: 0 2px 10px rgba(0,0,0,0.12);
    overflow: hidden;
  }
  .brand {
    position: absolute; right: 44px; top: 40px; text-align: right;
  }
  .brand-name {
    font-size: 30px; font-weight: 400; letter-spacing: 5px;
    color: var(--charcoal); line-height: 1;
  }
  .brand-tagline {
    margin-top: 4px; font-size: 5.5px; font-weight: 600;
    letter-spacing: 1.4px; color: var(--green); text-transform: uppercase;
  }
  .letter {
    position: absolute; left: 58px; top: 200px; width: 300px;
    font-size: 7.5px; line-height: 1.55; color: var(--ink);
  }
  .letter-date { margin-bottom: 14px; }
  .recipient { margin-bottom: 14px; }
  .salutation { font-weight: 700; color: var(--ink-dark); margin-bottom: 10px; }
  .letter p.body { margin-bottom: 10px; text-align: justify; }
  .closing { margin-top: 4px; }
  .signature {
    font-family: "Dancing Script", cursive;
    font-size: 22px; color: #9a9a9c; line-height: 1.2; margin: 2px 0 2px;
  }
  .wave { position: absolute; inset: 0; width: 524px; height: 740px; }
  .contact-list {
    position: absolute; right: 16px; top: 482px;
    list-style: none; text-align: right;
    font-size: 7.5px; line-height: 1.75; color: var(--white);
  }
  .contact-list li { display: flex; justify-content: flex-end; align-items: center; gap: 5px; }
  .contact-icon {
    width: 8px; height: 8px; border-radius: 50%;
    background: var(--green); display: inline-block; flex: none;
  }
  .address {
    position: absolute; left: 36px; bottom: 8px;
    display: flex; align-items: center; gap: 5px;
    font-size: 7.5px; color: var(--white);
  }
</style>
</head>
<body>
  <main class="letterhead">
    <header class="brand">
      <div class="brand-name">NORVALE</div>
      <div class="brand-tagline">Air Conditioning &amp; Refrigeration</div>
    </header>

    <section class="letter">
      <p class="letter-date">January 12, 2014</p>
      <p class="recipient">Mr. John Doe<br>President<br>AA Corporation<br>111 Street Name, Suite#<br>City, State, 12345</p>
      <p class="salutation">Dear Mr. John,</p>
      <p class="body">Lorem Ipsum is simply dummy text of the printing and typesetting industry. Lorem Ipsum has been the industry's standard dummy text ever since the 1500s, when an unknown printer took a galley of type and scrambled it to make a type specimen book. It has survived not only five centuries, but also the leap into electronic typesetting, remaining essentially unchanged.</p>
      <p class="body">The standard chunk of Lorem Ipsum used since the 1500s is reproduced below for those interested. Sections 1.10.32 and 1.10.33 from "de Finibus Bonorum et Malorum" by Cicero are also reproduced in their exact original form, accompanied by English versions from the 1914 translation by H. Rackham.</p>
      <p class="body">Lorem Ipsum is simply dummy text of the printing and typesetting industry. Lorem Ipsum has been the industry's standard dummy text ever since the 1500s, when an unknown printer took a galley of type and scrambled it to make a type specimen book. It has survived not only five centuries, but also the leap into electronic typesetting, remaining essentially unchanged. It was popularised in the</p>
      <p class="closing">Sincerely Your,</p>
      <p class="signature">your name</p>
      <p>Name Last Name<br>Company Name</p>
    </section>

    <svg class="wave" viewBox="0 0 524 740" aria-hidden="true">
      <path transform="translate(0,-24)" d="M0 714 C 250 705, 330 600, 390 500 C 430 435, 470 405, 524 398 L 524 764 L 0 764 Z" fill="var(--charcoal)"/>
      <path transform="translate(0,-16)" d="M0 714 C 250 705, 330 600, 390 500 C 430 435, 470 405, 524 398 L 524 756 L 0 756 Z" fill="var(--white)"/>
      <path transform="translate(0,-12)" d="M0 714 C 250 705, 330 600, 390 500 C 430 435, 470 405, 524 398 L 524 752 L 0 752 Z" fill="var(--green)"/>
      <path transform="translate(0,-5)" d="M0 714 C 250 705, 330 600, 390 500 C 430 435, 470 405, 524 398 L 524 745 L 0 745 Z" fill="var(--white)"/>
      <path d="M0 714 C 250 705, 330 600, 390 500 C 430 435, 470 405, 524 398 L 524 740 L 0 740 Z" fill="var(--coral)"/>
    </svg>

    <ul class="contact-list">
      <li>(00) 01234 567 890 <span class="contact-icon"></span></li>
      <li>(00) 01234 567 891 <span class="contact-icon"></span></li>
      <li>hello@norvaleair.com <span class="contact-icon"></span></li>
      <li>www.norvaleair.com <span class="contact-icon"></span></li>
    </ul>

    <p class="address"><span class="contact-icon"></span>Suite 102 Street name, State, Zip 2034, Country</p>
  </main>
</body>
</html>
```